Tampa Bay fishing guide needs stunning website.

I currently have a site - www.reelcoveguide.net which I personally put together using the Pagely platform and I am looking for a redesign on a different platform (Sitecraft?) that will allow me to easily create landing pages in the future. Would like to have a block for visitors to opt in to newsletter. Need social media links on all pages.

I would like to let my visitors know that I am able to handle their fishing charter needs here in the Tampa Bay area, if I'm not available for the dates they are looking to go I can refer them to a reputable captain in the area.

Target Market(s)

United States

Industry/Entity Type

Tourism

Coding

Coded - Design and coding required

Number of Pages Required

5+ page

Font styles to use
Sans Serif

Colors
0355a3
3176b5
85abd2
fbf289

Requirements
Must have
• Mobile Responsive, Ability to insert Vantor Metrics, Chatterbox pixels, ability to add custom landing pages in future
Nice to have
• Clean, easy navigation

```html
<!DOCTYPE html>
<html lang="en">
<head>
<meta charset="utf-8">
<title>Tampa Bay Fishing Guide – Captain Dale Brennick</title>
<link href="https://fonts.googleapis.com/css2?family=Open+Sans:wght@400;600;700;800&display=swap" rel="stylesheet">
<style>
:root{
  --blue:#0355a3;
  --mid:#3176b5;
  --light:#85abd2;
  --yellow:#fbf289;
  --ink:#33475b;
  --grey:#e9ebee;
  --white:#fff;
}
*{box-sizing:border-box;margin:0;padding:0}
html,body{width:1200px;height:2768px;overflow:hidden}
body{position:relative;background:var(--white);font-family:"Open Sans",Arial,sans-serif;color:var(--ink)}
.hero{position:absolute;left:0;top:0;width:1200px;height:560px;background:linear-gradient(120deg,#0b3d6e 0%,#2a6aa6 35%,#6f9fc9 60%,#a9c4dc 80%,#5a7f9f 100%)}
.hero-wave{position:absolute;left:0;top:430px;width:1200px;height:140px}
.nav{position:absolute;left:160px;top:30px;width:880px;height:60px;display:flex;align-items:center}
.brand{display:flex;align-items:center;gap:10px;color:var(--white);font-weight:800;font-size:28px}
.brand-dot{width:18px;height:18px;border-radius:50%;background:var(--light)}
.menu{margin-left:auto;display:flex;gap:26px;align-items:center;font-size:13px;font-weight:600;color:var(--white);letter-spacing:.5px}
.menu .active{border-bottom:2px solid var(--white);padding-bottom:4px}
.book{background:var(--light);color:var(--white);padding:8px 14px;border-radius:3px;font-size:13px}
.hero-copy{position:absolute;left:172px;top:218px;width:330px;color:var(--white);font-size:20px;line-height:1.45;font-weight:600}
.btn{display:inline-block;background:var(--yellow);color:var(--blue);font-weight:700;font-size:13px;letter-spacing:.5px;padding:11px 22px;border-radius:2px}
.hero .btn{position:absolute;left:172px;top:362px}
.dots{position:absolute;left:1132px;top:320px;display:flex;flex-direction:column;gap:10px}
.dots i{width:9px;height:9px;border-radius:50%;background:rgba(255,255,255,.6);display:block}
.dots i:first-child{background:var(--white)}
.intro{position:absolute;left:200px;top:556px;width:800px;text-align:center}
.intro h1{color:var(--blue);font-size:34px;font-weight:800;line-height:1.3}
.intro p{font-size:12.5px;line-height:1.6;margin-top:22px;color:#555}
.card{position:absolute;background:var(--blue);overflow:hidden}
.card .photo{position:absolute;left:0;top:0;width:100%}
.card .band{position:absolute;left:0;bottom:0;width:100%;height:100px;color:var(--white);padding:28px 24px}
.band h3{font-size:18px;font-weight:700}
.band p{font-size:14px;margin-top:4px}
.arrow{position:absolute;right:22px;bottom:30px;width:38px;height:38px}
.wide{position:absolute;left:172px;top:1405px;width:856px;height:386px;background:var(--blue)}
.wide .photo{position:absolute;left:0;top:0;width:520px;height:386px;background:linear-gradient(135deg,#6aa6cf,#9cc3dc 50%,#c9b79a)}
.wide h2{position:absolute;left:560px;top:120px;width:260px;color:var(--white);font-size:44px;font-weight:800;line-height:1.15;text-align:center}
.wide .btn{position:absolute;left:640px;top:268px}
.footer{position:absolute;left:0;top:2200px;width:1200px;height:568px;background:var(--grey)}
.footer-wave{position:absolute;left:0;top:2140px;width:1200px;height:80px}
.footer .brand{position:absolute;left:0;width:1200px;justify-content:center;top:80px;color:var(--blue)}
.footer .brand-dot{background:var(--mid)}
.cols{position:absolute;left:180px;top:200px;width:840px;display:flex;gap:60px;font-size:12px;line-height:1.9}
.cols h4{color:var(--blue);font-size:13px;font-weight:700;margin-bottom:14px}
.col1{width:220px}.col2{width:200px}.col3{width:260px}
.row{display:flex;align-items:center;gap:10px}
.input{border:1px solid #bbb;background:var(--white);height:30px;font-size:11px;color:#999;padding:6px 10px}
.subscribe{margin-top:10px;background:var(--blue);color:var(--white);font-weight:700;font-size:12px;text-align:center;padding:9px}
.pay{position:absolute;left:380px;top:384px;display:flex;gap:40px;font-size:12px;font-weight:700;color:var(--blue);align-items:center}
.sq{width:24px;height:15px;background:#8a97a6;display:inline-block;margin-left:4px}
.ci{width:14px;height:14px;border-radius:50%;background:var(--blue);display:inline-block;margin-left:6px}
.bottom-nav{position:absolute;left:0;width:1200px;top:448px;display:flex;justify-content:center;gap:18px;font-size:12px;color:#555}
.copy{position:absolute;left:0;width:1200px;top:490px;text-align:center;font-size:11px;color:#777}
</style>
</head>
<body>
<header class="hero">
  <div role="img" aria-label="Photo of a guide on a boat holding a fish with the bay behind" style="position:absolute;inset:0"></div>
  <nav class="nav">
    <div class="brand"><span class="brand-dot"></span>Brennick</div>
    <div class="menu">
      <span class="active">HOME</span><span>ABOUT US</span><span>PICK UP LOCATIONS</span><span>RATES</span><span>CONTACT US</span><span class="book">Book Now</span>
    </div>
  </nav>
  <p class="hero-copy">Come fish with Captain Dale Brennick, Tampa Bay, FL fishing guide, Tampa Bay's most respected Captain 25 year Native Guide</p>
  <span class="btn">LEARN MORE</span>
  <div class="dots"><i></i><i></i><i></i></div>
  <svg class="hero-wave" viewBox="0 0 1200 140" preserveAspectRatio="none"><path d="M0 90 C300 10 600 140 900 60 C1020 30 1120 40 1200 20 L1200 140 L0 140Z" fill="#fff"/></svg>
</header>

<section class="intro">
  <h1>Tampa Bay Fishing Guide Tampa Bay<br>Fishing Charter's</h1>
  <p>Capt. Dale Brennick, with over 25 years' experience, Native fishing charter guide offering full and half day fishing charters on the waters of Tampa Bay. If you're looking for a great fishing charter, do not hesitate to contact Capt. Dale or you can simply book your trip online here.</p>
  <p style="margin-top:14px">Come enjoy a wonderful day fishing inshore Tampa for Tarpon, Snook, Redfish, Trout, Sharks, Cobia, Spanish mackerel as well as others aboard Capt. Dale's boat. Capt. Dale will work hard to ensure that you and your guests have a memorable day enjoying the wonderful gamefish that Tampa Bay has to offer.</p>
</section>

<svg width="0" height="0" style="position:absolute"><symbol id="arr" viewBox="0 0 38 38"><circle cx="19" cy="19" r="19" fill="#fff" opacity=".9"/><path d="M16 11 L24 19 L16 27" stroke="#0355a3" stroke-width="3" fill="none"/></symbol></svg>

<article class="card" style="left:172px;top:1010px;width:424px;height:372px">
  <div class="photo" role="img" aria-label="Photo of an angler holding a catch on the water" style="height:272px;background:linear-gradient(135deg,#7fb3d6,#bcd6e6 60%,#c7ad8e)"></div>
  <div class="band"><h3>Photogallery</h3><p>Rosa Whitfield In Tampa Bay</p><svg class="arrow"><use href="#arr"/></svg></div>
</article>
<article class="card" style="left:612px;top:1010px;width:416px;height:372px">
  <div class="photo" role="img" aria-label="Portrait photo of the captain in a cap" style="height:272px;background:linear-gradient(160deg,#9ec2dc,#c6dbe8 50%,#9aa5ad)"></div>
  <div class="band"><h3>About Me</h3><p>Captian Brennick</p><svg class="arrow"><use href="#arr"/></svg></div>
</article>

<section class="wide">
  <div class="photo" role="img" aria-label="Photo of two anglers fishing from a boat"></div>
  <h2>Full&amp; Half Day Charter's</h2>
  <span class="btn">LEARN MORE</span>
</section>

<article class="card" style="left:172px;top:1802px;width:424px;height:372px">
  <div class="photo" role="img" aria-label="Photo of a large fish being landed beside the boat" style="height:272px;background:linear-gradient(135deg,#2f6f8c,#5fa2b8 55%,#a6c9d3)"></div>
  <div class="band"><h3>Pick Up Locations</h3><p>Locations in Tampa Bay</p><svg class="arrow"><use href="#arr"/></svg></div>
</article>
<article class="card" style="left:612px;top:1802px;width:416px;height:372px">
  <div class="photo" role="img" aria-label="Black and white photo of two anglers on a dock" style="height:272px;background:linear-gradient(135deg,#8c8c8c,#cfcfcf 55%,#6e6e6e)"></div>
  <div class="band"><h3>Mutiple Pick Up points</h3><p>Multiple locations in Tampa Bay</p><svg class="arrow"><use href="#arr"/></svg></div>
</article>

<svg class="footer-wave" viewBox="0 0 1200 80" preserveAspectRatio="none"><path d="M0 60 C300 0 500 70 800 30 C1000 5 1100 30 1200 10 L1200 80 L0 80Z" fill="#e9ebee"/></svg>
<footer class="footer">
  <div class="brand"><span class="brand-dot"></span>Brennick</div>
  <div class="cols">
    <div class="col1"><h4>Pickup Locations</h4><div>Gandy Bridge - St. Petersburg</div><div>Little Harbor - Ruskin</div><div>Gandy Boat Ramp</div><div>Bay Pier Boat Ramp</div></div>
    <div class="col2"><h4>Contact Us</h4>
      <div class="row"><svg width="12" height="12" viewBox="0 0 12 12"><path d="M2 1 L4 1 L5 4 L3.5 5 Q5 8 7 8.5 L8 7 L11 8 L11 10 Q6 11 2 6 Q1 3 2 1Z" fill="#0355a3"/></svg>813-555-0148</div>
      <div class="row"><svg width="12" height="10" viewBox="0 0 12 10"><rect x=".5" y=".5" width="11" height="9" fill="none" stroke="#0355a3"/><path d="M.5 .5 L6 5 L11.5 .5" fill="none" stroke="#0355a3"/></svg>dale@reelcoveguide.net</div>
    </div>
    <div class="col3"><h4>Newsletter Signup</h4><div class="input">Enter your email address</div><div class="subscribe">SUBSCRIBE NOW</div></div>
  </div>
  <div class="pay"><span>Payment Options <i class="sq"></i><i class="sq"></i><i class="sq"></i><i class="sq"></i></span><span>Connect With Us <i class="ci"></i></span></div>
  <div class="bottom-nav"><span>Home</span><span>|</span><span>About Us</span><span>|</span><span>Pick Up Locations</span><span>|</span><span>Rates</span><span>|</span><span>Contact Us</span></div>
  <div class="copy">© 2024 by Capt. Dale Brennick</div>
</footer>
</body>
</html>
```